Local Flower Farm Needs Business Card Design

I need business cards designed for a flower farm based in Eudora, Kansas.
Business Info:
We are a local cut flower farm located in Eudora, Kansas, founded by Corinne Haldwick. What started as a passion for agriculture and search for more joy in daily life has blossomed into a small business dedicated to providing the community with beautiful, fresh, and sustainable flowers. We specialize in local, seasonal blooms, ensuring that every petal reflects the care and dedication we pour into our craft. Our mission is to deliver the highest quality flowers directly to our customers through local farmers markets and to florists who share our commitment to sustainability. Join us in celebrating the beauty of nature, one bloom at a time!
Contact Details:
Corinne Haldwick
Owner
Phone 913-555-0147
Facebook: Rosalind Thorpe Gardens
Instagram: @RosalindThorpeGardens
Website: RosalindThorpeGardens.example
Target Market(s)
Wholesale to Florists and Direct to Consumer via Farmers Market
Industry/Entity Type
Florist, Farm
Contact Information for Business Card
Name, Contact Info, Logo
Look and feel
Each slider illustrates characteristics of the customer's brand and the style your logo design should communicate.

```html
<!DOCTYPE html>
<html lang="en">
<head>
<meta charset="utf-8">
<title>Rosalind Thorpe Gardens – Business Card</title>
<link rel="stylesheet" href="https://fonts.googleapis.com/css2?family=Cormorant+Garamond:wght@500&family=Roboto:wght@400;700&display=swap">
<style>
  :root {
    --backdrop: #1c1e21;
    --card: #0d3037;
    --card-edge: #0a262c;
    --ink: #ffffff;
    --ink-soft: #d7e3e4;
    --rule: #c9d5d6;
  }
  * { box-sizing: border-box; margin: 0; padding: 0; }
  html, body { width: 1200px; height: 900px; overflow: hidden; }
  body {
    background: var(--backdrop);
    display: flex;
    align-items: center;
    justify-content: center;
    gap: 50px;
    font-family: "Roboto", Arial, sans-serif;
    color: var(--ink);
  }
  .card {
    width: 525px;
    height: 300px;
    background: linear-gradient(160deg, #10373f 0%, var(--card) 55%, var(--card-edge) 100%);
    border-radius: 4px;
    box-shadow: 0 14px 30px rgba(0,0,0,.45);
    position: relative;
  }
  .brand-mark {
    display: flex;
    flex-direction: column;
    align-items: center;
    gap: 10px;
  }
  .brand-ring {
    width: 92px; height: 92px;
    border: 1.5px solid var(--ink);
    border-radius: 50%;
  }
  .brand-name {
    font-family: "Cormorant Garamond", Georgia, serif;
    font-weight: 500;
    font-size: 17px;
    letter-spacing: 3px;
    text-transform: uppercase;
    color: var(--ink);
    text-align: center;
  }
  .card--front {
    display: flex; align-items: center; justify-content: center;
  }
  .card--back {
    display: flex; align-items: center;
    padding: 0 34px;
  }
  .card--back .brand-mark { width: 190px; }
  .card--back .brand-ring { width: 80px; height: 80px; }
  .card--back .brand-name { font-size: 14px; letter-spacing: 2px; }
  .divider {
    width: 1.5px; height: 150px;
    background: var(--rule);
    margin: 0 26px 0 16px;
  }
  .contact-name {
    font-weight: 700; font-size: 22px; text-transform: uppercase;
    letter-spacing: .3px;
  }
  .contact-role { font-size: 13px; color: var(--ink-soft); margin-bottom: 18px; }
  .contact-list { list-style: none; font-size: 14.5px; line-height: 1.55; }
  .contact-list li { display: flex; align-items: center; gap: 8px; white-space: nowrap; }
  .contact-icon { width: 11px; height: 11px; flex: none; }
</style>
</head>
<body>
  <section class="card card--back">
    <div class="brand-mark">
      <div class="brand-ring"></div>
      <div class="brand-name">Rosalind Thorpe Gardens</div>
    </div>
    <div class="divider"></div>
    <div class="contact">
      <h1 class="contact-name">Corinne Haldwick</h1>
      <p class="contact-role">Owner</p>
      <ul class="contact-list">
        <li>
          <svg class="contact-icon" viewBox="0 0 24 24" fill="#fff"><path d="M6.6 10.8a15.1 15.1 0 0 0 6.6 6.6l2.2-2.2a1 1 0 0 1 1-.25 11.4 11.4 0 0 0 3.6.57 1 1 0 0 1 1 1V20a1 1 0 0 1-1 1A17 17 0 0 1 3 4a1 1 0 0 1 1-1h3.5a1 1 0 0 1 1 1c0 1.25.2 2.45.57 3.57a1 1 0 0 1-.25 1z"/></svg>
          913-555-0147
        </li>
        <li>
          <svg class="contact-icon" viewBox="0 0 12 12"><circle cx="6" cy="6" r="5" fill="#fff"/></svg>
          Rosalind Thorpe Gardens
        </li>
        <li>
          <svg class="contact-icon" viewBox="0 0 12 12"><rect x="1" y="1" width="10" height="10" rx="2" fill="none" stroke="#fff" stroke-width="1.5"/></svg>
          @RosalindThorpeGardens
        </li>
        <li>
          <svg class="contact-icon" viewBox="0 0 12 12" fill="none" stroke="#fff" stroke-width="1.1"><circle cx="6" cy="6" r="5"/><ellipse cx="6" cy="6" rx="2.2" ry="5"/><path d="M1 6h10"/></svg>
          RosalindThorpeGardens.example
        </li>
      </ul>
    </div>
  </section>

  <section class="card card--front">
    <div class="brand-mark">
      <div class="brand-ring"></div>
      <div class="brand-name">Rosalind Thorpe Gardens</div>
    </div>
  </section>
</body>
</html>
```